Photography Business, Business Card

Looking for a unique cutting edge card that takes advantage of the latest printing technologies. Please review this site for all the options they office: https://glowprintly.com. If you can think it they can do it. And if you have an idea and do not know if they can do it, I will check into it.

Target Market(s)

People and places I took images of and future clients.

Industry/Entity Type

Photography

Contact Information for Business Card

Name, cell & email. Derek Holloway, dholloway@kpnvisuals.com, 312-555-0148

Colors

Designer to choose only greyscale colors for use in the design.

Requirements
Must have
• 100% cutting edge. Is so great, those I hand it to always show it to someone else. A piece of art.
Nice to have
• Blacks, silvers, greys, some red. Maybe other colors?

```html
<!DOCTYPE html>
<html lang="en">
<head>
<meta charset="utf-8">
<title>Derek Holloway Photography – Business Card</title>
<link rel="stylesheet" href="https://fonts.googleapis.com/css2?family=Allura&family=Montserrat:wght@400;500;600&display=swap">
<style>
  :root {
    --backdrop: #2b2b2b;
    --card-black: #0e0e0e;
    --silver: #cfcfcf;
    --silver-soft: #a9a9a9;
    --edge-red: #e11b22;
  }
  * { margin: 0; padding: 0; box-sizing: border-box; }
  html, body { width: 1200px; height: 800px; overflow: hidden; }
  body {
    background: var(--backdrop);
    position: relative;
    font-family: "Montserrat", sans-serif;
    color: var(--silver);
  }
  .card {
    position: absolute;
    background: var(--card-black);
    box-shadow: 0 3px 0 var(--edge-red), 0 18px 40px rgba(0,0,0,0.55);
  }
  /* Front card: rounded arch top */
  .card-front {
    left: 140px; top: 110px;
    width: 360px; height: 580px;
    border-radius: 180px 180px 18px 18px;
  }
  .brand-ring {
    position: absolute;
    left: 40px; top: 40px;
    width: 280px; height: 280px;
    border: 6px solid var(--silver);
    border-radius: 50%;
    display: flex; align-items: center; justify-content: center;
  }
  .brand-name {
    font-family: "Montserrat", sans-serif;
    font-weight: 500;
    font-size: 30px;
    letter-spacing: 4px;
    color: var(--silver);
  }
  .signature {
    position: absolute;
    left: 36px; top: 350px;
    width: 290px;
  }
  .signature-name {
    font-family: "Allura", cursive;
    font-size: 48px;
    line-height: 1;
    white-space: nowrap;
    color: var(--silver);
  }
  .signature-tag {
    display: block;
    text-align: right;
    font-size: 10px;
    letter-spacing: 4px;
    color: var(--silver-soft);
    margin-top: 4px;
  }
  .contact-list {
    position: absolute;
    left: 40px; bottom: 40px;
    list-style: none;
    font-size: 15px;
    line-height: 1.75;
    color: var(--silver);
  }
  .contact-list li { display: flex; align-items: center; gap: 10px; }
  .contact-icon { width: 14px; height: 14px; flex: none; }
  /* Back card: round left end */
  .card-back {
    left: 560px; top: 240px;
    width: 540px; height: 340px;
    border-radius: 170px 18px 18px 170px;
    display: flex; align-items: center; justify-content: center;
  }
  .back-mark {
    font-family: "Montserrat", sans-serif;
    font-weight: 500;
    font-size: 52px;
    letter-spacing: 6px;
    color: var(--silver);
    padding-left: 50px;
  }
</style>
</head>
<body>
  <section class="card card-front">
    <div class="brand-ring"><span class="brand-name">HOLLOWAY</span></div>
    <div class="signature">
      <div class="signature-name">Derek Holloway</div>
      <span class="signature-tag">PHOTOGRAPHY</span>
    </div>
    <ul class="contact-list">
      <li>
        <svg class="contact-icon" viewBox="0 0 14 14" aria-hidden="true"><rect x="3.5" y="1" width="7" height="12" rx="1.2" fill="none" stroke="currentColor" stroke-width="1.4"/><circle cx="7" cy="11" r="0.8" fill="currentColor"/></svg>
        312-555-0148
      </li>
      <li>
        <svg class="contact-icon" viewBox="0 0 14 14" aria-hidden="true"><rect x="1" y="3" width="12" height="8" fill="currentColor"/><path d="M1 3 L7 8 L13 3" fill="none" stroke="#0e0e0e" stroke-width="1.2"/></svg>
        dholloway@kpnvisuals.com
      </li>
      <li>
        <svg class="contact-icon" viewBox="0 0 14 14" aria-hidden="true"><circle cx="7" cy="7" r="5.6" fill="none" stroke="currentColor" stroke-width="1.3"/><ellipse cx="7" cy="7" rx="2.4" ry="5.6" fill="none" stroke="currentColor" stroke-width="1"/><line x1="1.4" y1="7" x2="12.6" y2="7" stroke="currentColor" stroke-width="1"/></svg>
        www.kpnvisuals.com
      </li>
    </ul>
  </section>

  <section class="card card-back">
    <span class="back-mark">HOLLOWAY</span>
  </section>
</body>
</html>
```